Telecommunications Company needs a business card design

We are looking for a sleek, professional and modern business card design based off our new logo. Will look at both light and dark options. On some designs please provide a small space for a QR code

Target Market(s)

B2B clients in Australia

Contact Information for Business Card

Name, Position, Brisbane (head) office, Phone number, email address, QR code (link to our website qlinetelecom.com.au

Colors
0054AA
0677BA
7BADD7
CADEEF
E8F1F8
0094D4
00A9DD
6FCCEA
C7EBF8
E9F6FB
00AB8E
00BBA5
67D7C9
C6EFE9
E9F9F6

```html
<!DOCTYPE html>
<html lang="en">
<head>
<meta charset="UTF-8">
<title>Qline Communications – Business Cards</title>
<link rel="stylesheet" href="https://fonts.googleapis.com/css2?family=Montserrat:wght@400;500;600;800&display=swap">
<style>
  :root {
    --backdrop: #e4e6e9;
    --card-dark: #07080a;
    --card-light: #ffffff;
    --blue-deep: #0054AA;
    --blue-mid: #0677BA;
    --teal: #00A9DD;
    --aqua: #00BBA5;
    --ink: #1d1f22;
    --slate: #8a9099;
  }
  * { margin: 0; padding: 0; box-sizing: border-box; }
  html, body { width: 1200px; height: 900px; overflow: hidden; }
  body {
    background: var(--backdrop);
    font-family: "Montserrat", sans-serif;
    position: relative;
  }
  .card {
    position: absolute;
    width: 560px;
    height: 320px;
    border-radius: 22px;
    overflow: hidden;
    box-shadow: 0 10px 30px rgba(0,0,0,0.18);
  }
  .card--front {
    left: 80px; top: 90px;
    background: var(--card-dark);
    display: flex; align-items: center; justify-content: center;
  }
  .brand-mark {
    display: flex; align-items: center; gap: 14px;
    font-weight: 600;
    font-size: 34px;
    letter-spacing: 0.5px;
    color: var(--aqua);
  }
  .brand-mark__square {
    width: 22px; height: 22px;
    background: var(--aqua);
  }
  .card--back {
    left: 560px; top: 490px;
    background: var(--card-light);
  }
  .card__brand {
    position: absolute; left: 40px; top: 42px;
    font-weight: 600; font-size: 22px;
    color: var(--blue-mid);
  }
  .card__person {
    position: absolute; right: 44px; top: 36px;
    text-align: right;
  }
  .card__name {
    font-weight: 800; font-size: 22px;
    color: var(--blue-mid);
    letter-spacing: 0.3px;
  }
  .card__role {
    font-size: 13px; color: var(--ink);
    margin-top: 2px;
  }
  .card__tab {
    position: absolute; right: 0; top: 34px;
    width: 14px; height: 30px;
    background: var(--blue-mid);
  }
  .card__office {
    position: absolute; right: 44px; top: 170px;
    font-size: 14px; color: var(--ink);
  }
  .card__rule {
    position: absolute; left: 40px; right: 40px; top: 200px;
    height: 2px; background: var(--teal);
  }
  .contact-list {
    position: absolute; left: 40px; top: 218px;
    list-style: none;
    font-size: 13px; color: var(--ink);
  }
  .contact-list li {
    display: flex; align-items: center; gap: 8px;
    line-height: 22px;
  }
  .contact-list svg { width: 11px; height: 11px; fill: var(--blue-mid); }
</style>
</head>
<body>
  <section class="card card--front">
    <div class="brand-mark">
      <span class="brand-mark__square"></span>
      <span>Qline Communications</span>
    </div>
  </section>

  <section class="card card--back">
    <div class="card__brand">Qline Communications</div>
    <div class="card__tab"></div>
    <div class="card__person">
      <div class="card__name">MARK ELLISON</div>
      <div class="card__role">Director</div>
    </div>
    <div class="card__office">Brisbane (head) office</div>
    <div class="card__rule"></div>
    <ul class="contact-list">
      <li>
        <svg viewBox="0 0 16 16"><path d="M3 1h3l1.5 4-2 1.3a9 9 0 0 0 4.2 4.2L11 8.5l4 1.5v3a2 2 0 0 1-2 2A13 13 0 0 1 1 3a2 2 0 0 1 2-2z"/></svg>
        (07) 3100 2480
      </li>
      <li>
        <svg viewBox="0 0 16 16"><path d="M1 3h14v10H1zM2.5 4.5v.4L8 9l5.5-4.1v-.4zM2.5 6.8v4.7h11V6.8L8 10.9z"/></svg>
        qlinetelecom.com.au
      </li>
      <li>
        <svg viewBox="0 0 16 16"><circle cx="8" cy="8" r="7"/><path d="M1 8h14M8 1c3 3 3 11 0 14M8 1c-3 3-3 11 0 14" stroke="#fff" stroke-width="1" fill="none"/></svg>
        qlinetelecom.com.au
      </li>
    </ul>
  </section>
</body>
</html>
```